Indy Film Production Company/Studio

We need a business card designed from an existing logo. We are a digital studio/production company that caters to creating genre entertainment, like Action, Horror, and martial arts. The card along with the logo will be used to Brand the company from letter heads to banners. The design will also be used for postcards and Brochures. It should be professional and masculine.
Updates

Thank you to all the designers who have participated. I'm narrowing down who it will be. Thank you again.

Target Market(s)

Investors, Networks, Producers, and actors

Industry/Entity Type

Film Production

Contact Information for Business Card

Teodoro Valbuena
Producer/Writer/Director
www.kestrelpicturehouse.example

Requirements
Must have
• Website address, Facebook icon and Twitter icon possibly in the back of the card.
Nice to have
• Logline of Company: Follow The Action.

```html
<!DOCTYPE html>
<html lang="en">
<head>
<meta charset="utf-8">
<title>Kestrel Picture House — Business Card</title>
<link rel="stylesheet" href="https://fonts.googleapis.com/css2?family=Roboto:wght@400;500&family=Roboto+Condensed:wght@700&display=swap">
<style>
  :root {
    --stage: #e9e7e3;
    --charcoal: #3a3a3b;
    --charcoal-dark: #2c2c2d;
    --paper: #ffffff;
    --brand-red: #e3202a;
    --ink: #333333;
    --rule: #c9c9c9;
    --muted: #d8d8d8;
  }
  * { box-sizing: border-box; margin: 0; padding: 0; }
  html, body { width: 1200px; height: 950px; overflow: hidden; }
  body {
    background: var(--stage);
    position: relative;
    font-family: "Roboto", Arial, sans-serif;
  }
  .card {
    position: absolute;
    width: 630px;
    height: 360px;
    border-radius: 6px;
    overflow: hidden;
    box-shadow: 0 10px 28px rgba(0,0,0,.18);
  }

  /* Back of card */
  .card-back {
    left: 70px; top: 70px;
    background: linear-gradient(160deg, var(--charcoal) 0%, var(--charcoal-dark) 100%);
    color: var(--paper);
  }
  .social-squares {
    position: absolute; top: 20px; right: 22px;
    display: flex; gap: 4px;
  }
  .social-squares span {
    width: 22px; height: 22px; background: var(--paper); border-radius: 2px;
  }
  .back-brand {
    position: absolute; left: 0; right: 0; top: 118px;
    text-align: center;
  }
  .wordmark {
    font-family: "Roboto Condensed", "Arial Narrow", sans-serif;
    font-weight: 700;
    text-transform: uppercase;
    line-height: 1;
  }
  .back-brand .wordmark-initials { font-size: 96px; letter-spacing: 2px; }
  .back-brand .wordmark-name { font-size: 24px; letter-spacing: 3px; margin-top: 6px; }
  .back-url {
    position: absolute; left: 0; right: 0; bottom: 52px;
    text-align: center; font-size: 15px; letter-spacing: 2.5px; color: var(--muted);
  }

  /* Front of card */
  .card-front {
    left: 500px; top: 500px;
    background: var(--paper);
  }
  .front-brand {
    position: absolute; right: 40px; top: 36px;
    color: var(--brand-red); text-align: center;
  }
  .front-brand .wordmark-initials { font-size: 72px; letter-spacing: 2px; }
  .front-brand .wordmark-name { font-size: 17px; letter-spacing: 2px; margin-top: 4px; }
  .brand-rule {
    position: absolute; left: 250px; right: 40px; top: 150px;
    height: 1px; background: var(--rule);
  }
  .person {
    position: absolute; left: 40px; top: 190px;
  }
  .person-name { color: var(--brand-red); font-size: 22px; font-weight: 500; }
  .person-role { color: var(--ink); font-size: 15px; margin-top: 4px; }
  .mid-rule {
    position: absolute; left: 0; top: 246px; width: 390px; height: 1px; background: var(--rule);
  }
  .mid-band {
    position: absolute; left: 390px; right: 0; top: 238px; height: 16px;
    background: var(--charcoal);
  }
  .mid-band::before {
    content: ""; position: absolute; left: 0; top: 0; width: 8px; height: 100%;
    background: var(--brand-red);
  }
  .contacts {
    position: absolute; left: 40px; top: 262px;
    list-style: none;
  }
  .contacts li {
    display: flex; align-items: center; gap: 8px;
    font-size: 14px; color: var(--ink); height: 22px;
  }
  .contacts svg { width: 14px; height: 14px; flex: none; }
  .foot-band {
    position: absolute; left: 0; right: 0; bottom: 0; height: 14px;
    background: var(--brand-red);
    border-top: 3px solid var(--muted);
  }
</style>
</head>
<body>

<section class="card card-back" aria-label="Card back">
  <div class="social-squares" aria-hidden="true"><span></span><span></span></div>
  <div class="back-brand">
    <div class="wordmark wordmark-initials">KPH</div>
    <div class="wordmark wordmark-name">Kestrel Picture House</div>
  </div>
  <p class="back-url">www.kestrelpicturehouse.example</p>
</section>

<section class="card card-front" aria-label="Card front">
  <div class="front-brand">
    <div class="wordmark wordmark-initials">KPH</div>
    <div class="wordmark wordmark-name">Kestrel Picture House</div>
  </div>
  <div class="brand-rule"></div>

  <div class="person">
    <p class="person-name">Teodoro Valbuena</p>
    <p class="person-role">Producer/Writer/Director</p>
  </div>
  <div class="mid-rule"></div>
  <div class="mid-band"></div>

  <ul class="contacts">
    <li>
      <svg viewBox="0 0 14 14" aria-hidden="true"><circle cx="7" cy="7" r="7" fill="var(--brand-red)"/><path d="M4 4.5c0 3 2.5 5.5 5.5 5.5l.8-1.3-1.6-.8-.7.7c-1-.4-1.8-1.2-2.2-2.2l.7-.7-.8-1.6z" fill="#fff"/></svg>
      555 0142 7781
    </li>
    <li>
      <svg viewBox="0 0 14 14" aria-hidden="true"><circle cx="7" cy="7" r="7" fill="var(--brand-red)"/><rect x="3.5" y="4.5" width="7" height="5" fill="#fff"/><path d="M3.5 4.5 7 7.3l3.5-2.8" fill="none" stroke="var(--brand-red)" stroke-width=".8"/></svg>
      teo@kestrelpicturehouse.example
    </li>
    <li>
      <svg viewBox="0 0 14 14" aria-hidden="true"><circle cx="7" cy="7" r="7" fill="var(--brand-red)"/><circle cx="7" cy="7" r="3.6" fill="none" stroke="#fff" stroke-width=".9"/><path d="M3.4 7h7.2M7 3.4c-1.6 2-1.6 5.2 0 7.2M7 3.4c1.6 2 1.6 5.2 0 7.2" fill="none" stroke="#fff" stroke-width=".8"/></svg>
      www.kestrelpicturehouse.example
    </li>
  </ul>
  <div class="foot-band"></div>
</section>

</body>
</html>
```